We need a logo for our business which is a dental clinic (i.e. dentistry).
We would lilke designs using the colour blue, green and black incorporating the words Corvath Dental, possibly a smile or a tooth image can be considered for incorporation in the logo.

Industry/Entity Type

Dental

```html
<!DOCTYPE html>
<html lang="en">
<head>
<meta charset="utf-8">
<title>Corvath Dental — Business Card</title>
<link href="https://fonts.googleapis.com/css2?family=Marcellus+SC&display=swap" rel="stylesheet">
<style>
  :root {
    --page-bg: #e8e6e2;
    --card-bg: #ffffff;
    --brand-blue: #21afd0;
    --brand-blue-deep: #1594b5;
    --brand-green: #a6cf3a;
    --ink: #3a3a3a;
    --ink-soft: #555555;
    --divider: #9a9a9a;
  }
  html, body {
    margin: 0;
    padding: 0;
    width: 1200px;
    height: 900px;
    overflow: hidden;
    background: var(--page-bg);
    font-family: "Marcellus SC", serif;
  }
  .canvas {
    position: relative;
    width: 1200px;
    height: 900px;
  }
  .business-card {
    position: absolute;
    left: 100px;
    top: 160px;
    width: 1000px;
    height: 580px;
    background: var(--card-bg);
    border-radius: 44px;
    overflow: hidden;
    box-shadow: 0 10px 30px rgba(0,0,0,0.12);
  }
  .card-edges {
    position: absolute;
    inset: 0;
  }
  .brand-lockup {
    position: absolute;
    top: 130px;
    left: 0;
    right: 0;
    display: flex;
    justify-content: center;
    align-items: center;
    gap: 18px;
  }
  .brand-dot {
    width: 46px;
    height: 46px;
    border-radius: 50%;
    background: var(--brand-blue);
  }
  .brand-name {
    font-size: 54px;
    color: var(--brand-blue);
    letter-spacing: 1px;
    line-height: 1;
  }
  .contact-block {
    position: absolute;
    top: 330px;
    left: 0;
    right: 0;
    display: flex;
    justify-content: center;
  }
  .person {
    text-align: right;
    padding-right: 26px;
    color: var(--ink);
  }
  .person-name {
    font-size: 26px;
    letter-spacing: 2px;
    margin: 0;
  }
  .person-title {
    font-size: 19px;
    letter-spacing: 2px;
    margin: 4px 0 14px;
    color: var(--ink-soft);
  }
  .person-address {
    font-size: 19px;
    letter-spacing: 2px;
    line-height: 1.35;
    margin: 0;
    color: var(--ink-soft);
  }
  .divider {
    width: 2px;
    background: var(--divider);
    height: 170px;
  }
  .contact-list {
    list-style: none;
    margin: 0;
    padding: 0 0 0 22px;
    color: var(--ink);
    font-size: 20px;
    letter-spacing: 2px;
  }
  .contact-list li {
    display: flex;
    align-items: center;
    gap: 10px;
    height: 30px;
  }
  .contact-icon {
    width: 20px;
    height: 20px;
    flex: none;
  }
</style>
</head>
<body>
<main class="canvas">
  <section class="business-card">
    <svg class="card-edges" viewBox="0 0 1000 580" width="1000" height="580" aria-hidden="true">
      <defs>
        <linearGradient id="bandBlue" x1="0" y1="0" x2="1" y2="0">
          <stop offset="0" stop-color="var(--brand-blue-deep)"/>
          <stop offset="1" stop-color="var(--brand-blue)"/>
        </linearGradient>
      </defs>
      <path d="M0 0 H88 Q40 290 66 580 H0 Z" fill="url(#bandBlue)"/>
      <path d="M112 0 Q62 290 92 580" fill="none" stroke="var(--brand-green)" stroke-width="8"/>
      <path d="M1000 0 H910 Q950 290 898 580 H1000 Z" fill="url(#bandBlue)"/>
      <path d="M884 0 Q922 290 872 580" fill="none" stroke="var(--brand-green)" stroke-width="8"/>
    </svg>

    <div class="brand-lockup">
      <span class="brand-dot"></span>
      <span class="brand-name">Corvath Dental</span>
    </div>

    <div class="contact-block">
      <div class="person">
        <p class="person-name">Dana Merrow</p>
        <p class="person-title">Owner / C.E.O</p>
        <p class="person-address">Suite # 418, Elm Bldg,<br>NY 10452</p>
      </div>
      <div class="divider"></div>
      <ul class="contact-list">
        <li>
          <svg class="contact-icon" viewBox="0 0 20 20" aria-hidden="true"><circle cx="10" cy="10" r="10" fill="var(--ink)"/><path d="M6.5 5.5c0.8-0.6 1.5 0 2 1l0.5 1.2c0.2 0.6-0.6 1-0.6 1.4 0.4 1.2 1.4 2.3 2.6 2.7 0.4 0 0.8-0.8 1.4-0.6l1.2 0.5c1 0.5 1.6 1.2 1 2-1.5 1.8-4 1-6-1s-3-4.6-2.1-7.2z" fill="#fff"/></svg>
          555-218-4403
        </li>
        <li>
          <svg class="contact-icon" viewBox="0 0 20 20" aria-hidden="true"><circle cx="10" cy="10" r="10" fill="var(--ink)"/><rect x="7" y="4" width="6" height="12" rx="1.2" fill="#fff"/><rect x="8" y="5.5" width="4" height="7" fill="var(--ink)"/></svg>
          555-731-9026
        </li>
        <li>
          <svg class="contact-icon" viewBox="0 0 20 20" aria-hidden="true"><circle cx="10" cy="10" r="10" fill="var(--ink)"/><rect x="5" y="8" width="10" height="7" rx="1" fill="#fff"/><rect x="7" y="4.5" width="6" height="4" fill="#fff"/></svg>
          555-604-2175
        </li>
        <li>
          <svg class="contact-icon" viewBox="0 0 20 20" aria-hidden="true"><circle cx="10" cy="10" r="10" fill="var(--ink)"/><rect x="5" y="6.5" width="10" height="7" fill="#fff"/><path d="M5 6.5 L10 10.5 L15 6.5" fill="none" stroke="var(--ink)" stroke-width="1"/></svg>
          name@Corvathdental.com
        </li>
        <li>
          <svg class="contact-icon" viewBox="0 0 20 20" aria-hidden="true"><circle cx="10" cy="10" r="10" fill="var(--ink)"/><circle cx="10" cy="10" r="5.5" fill="none" stroke="#fff" stroke-width="1.2"/><ellipse cx="10" cy="10" rx="2.2" ry="5.5" fill="none" stroke="#fff" stroke-width="1"/><line x1="4.5" y1="10" x2="15.5" y2="10" stroke="#fff" stroke-width="1"/></svg>
          www.Corvathdental.com
        </li>
      </ul>
    </div>
  </section>
</main>
</body>
</html>
```